One page flyer for nonprofit focused IT company

I need a one page flyer (one side of a single 8.5x11 page) with text and graphics. The company logo is already done, and it must appear on the flyer along with other icons and graphics. The final design will be printed on heavy weight glossy paper as a handout and also distributed as a PDF.

The text is provided in an attachment, if it needs to be shortened let me know.

Industry/Entity Type

Information Technology

Requirements
Must have
• some flare (colors, icons or images)
Should not have
• While we work for nonprofits, my company is a FOR PROFIT company.

```html
<!DOCTYPE html>
<html lang="en">
<head>
<meta charset="utf-8">
<title>Kestrel Point Technologies – 50 Years of Nonprofit IT Services</title>
<link href="https://fonts.googleapis.com/css2?family=Playfair+Display:wght@400;700;900&family=Roboto:wght@400;700&display=swap" rel="stylesheet">
<style>
  :root{
    --brand-red:#9b2a33;
    --charcoal:#2e2e2e;
    --ink:#333333;
    --muted:#8a8a8a;
    --paper:#fbfbfb;
    --backdrop:#e9e9e9;
    --rule:#9a9a9a;
    --serif:"Playfair Display", Georgia, serif;
    --sans:"Roboto", Arial, sans-serif;
  }
  *{box-sizing:border-box;margin:0;padding:0}
  html,body{width:1200px;height:613px;overflow:hidden;background:var(--backdrop)}
  .canvas{position:relative;width:1200px;height:613px}
  .flyer{position:absolute;left:372px;top:11px;width:456px;height:591px;background:var(--paper);box-shadow:0 2px 10px rgba(0,0,0,.18);color:var(--ink);font-family:var(--sans);overflow:hidden}
  .abs{position:absolute}
  .flyer h1,.flyer h2,.flyer h3{font-variant-numeric:lining-nums}

  /* brand */
  .brand{left:0;width:456px;top:40px;display:flex;justify-content:center;align-items:center;gap:8px}
  .brand-square{width:14px;height:14px;background:var(--brand-red)}
  .brand-name{font-family:var(--serif);font-weight:400;color:var(--brand-red);font-size:18px;line-height:1;letter-spacing:.5px}

  /* headline */
  .headline{left:0;width:456px;top:92px;text-align:center;font-family:var(--serif);font-weight:900;color:var(--brand-red);font-size:73px;line-height:1;letter-spacing:-.5px;white-space:nowrap}
  .rule{left:18px;width:420px;border-top:1px dotted var(--rule)}
  .rule-top{top:166px}
  .rule-bottom{top:193px}
  .subhead{left:18px;width:420px;top:171px;text-align:center;font-family:var(--serif);font-weight:400;font-size:15.5px;letter-spacing:5.6px;color:var(--ink);line-height:1.1;white-space:nowrap}

  /* stories */
  .story{width:198px}
  .story-left{left:20px}
  .story-right{left:238px}
  .story h2{font-family:var(--serif);font-weight:400;font-size:9.3px;line-height:1.25;color:var(--ink)}
  .story h2 .accent{color:var(--brand-red)}
  .story p{margin-top:8px;font-size:5.7px;line-height:1.45;text-align:justify}
  .divider{left:227px;top:207px;height:143px;border-left:1px dotted var(--rule)}

  /* service grid */
  .services{left:19px;top:378px;width:419px;height:197px;display:grid;grid-template-columns:repeat(3,1fr);grid-template-rows:1fr 1fr}
  .tile{display:flex;flex-direction:column;align-items:center;justify-content:center;text-align:center;padding:6px 10px}
  .tile svg{width:20px;height:20px;margin-bottom:7px;fill:none;stroke-width:1.4;stroke-linecap:round;stroke-linejoin:round}
  .tile h3{font-family:var(--serif);font-weight:700;font-size:9.5px;line-height:1.2;color:var(--ink)}
  .tile h3 .accent{color:var(--brand-red)}
  .tile p{margin-top:6px;font-size:5.6px;line-height:1.5}
  .tile-light svg{stroke:var(--muted)}
  .tile-dark{background:var(--charcoal);color:#fff}
  .tile-dark h3{color:#fff}
  .tile-dark svg{stroke:#e6e6e6}
  .tile-red{background:var(--brand-red);color:#fff}
  .tile-red h3{color:#fff}
  .tile-red svg{stroke:#f1dada}
</style>
</head>
<body>
<div class="canvas">
  <article class="flyer">
    <div class="abs brand">
      <span class="brand-square"></span>
      <span class="brand-name">Kestrel Point Technologies</span>
    </div>

    <h1 class="abs headline">50 YEARS</h1>
    <div class="abs rule rule-top"></div>
    <div class="abs subhead">OF NONPROFIT IT SERVICES</div>
    <div class="abs rule rule-bottom"></div>

    <section class="abs story story-left" style="top:206px">
      <h2><span class="accent">An Efficient &amp; Elegant Approach</span><br>to IT Solution Implementations</h2>
      <p>Kestrel Point Technologies has been supporting the Information Systems needs of nonprofits for over 50 years. We continually strive to bring the latest technologies and best practices to nonprofits to drive down the cost of IT while implementing systems that drive revenue. Our Agile approach to IT management means that we deliver working systems to every one of our clients every two weeks.</p>
    </section>
    <section class="abs story story-left" style="top:295px">
      <h2><span class="accent">10x Increase in</span> Membership</h2>
      <p>Greenway Paths Conservancy needed to move to online membership registration and contracted with Kestrel Point Technologies to build a significant online presence and engage potential members. Through compelling online tools and mobile applications Greenway Paths has <b>increased membership 10 fold.</b></p>
    </section>

    <div class="abs divider"></div>

    <section class="abs story story-right" style="top:206px">
      <h2><span class="accent">Successes 90% Reduction in</span><br>Software Development Costs</h2>
      <p>Hartwell National Auto Retailers Association needed to update their core product offering; they engaged their in-house IT department who estimated the project would take 3 years at a cost of $3,000,000. HNARA decided to work with Kestrel Point Technologies instead, and the product was released to production in only 9 months at <b>one tenth of the cost</b>, only $300,000</p>
    </section>
    <section class="abs story story-right" style="top:295px">
      <h2><span class="accent">20% Reduction</span> in Overhead</h2>
      <p>The National Alliance for Women's Progress had antiquated systems and processes in place to manage over 500 chapters across the nation. Working with KPT they implemented online tools to allow communication and management between the local chapters and national headquarters. This eliminated much of the overhead of chapter management, <b>reducing HR costs by 20%.</b></p>
    </section>

    <section class="abs services">
      <div class="tile tile-light">
        <svg viewBox="0 0 24 24" aria-hidden="true"><rect x="2" y="4" width="17" height="11" rx="1"/><path d="M8 19h6M11 15v4"/><path d="M16 11l5 5-2 .5 1.5 2.5-1 .6-1.5-2.5-1.5 1.4z"/></svg>
        <h3><span class="accent">Solutions</span> Web Applications</h3>
        <p>With a focus on non-profit websites &amp; web based applications, KPT helps nonprofits communicate with their members &amp; donors while maximizing online giving &amp; engagement.</p>
      </div>
      <div class="tile tile-dark">
        <svg viewBox="0 0 24 24" aria-hidden="true"><rect x="7" y="2" width="10" height="20" rx="1.5"/><path d="M11 19h2"/></svg>
        <h3>Mobile Applications</h3>
        <p>Kestrel Point Technologies implements mobile applications for phones and tablets to provide direct communications with members and donors enabling real-time, two way interaction.</p>
      </div>
      <div class="tile tile-light">
        <svg viewBox="0 0 24 24" aria-hidden="true"><circle cx="12" cy="12" r="3"/><path d="M12 4v2M12 18v2M4 12h2M18 12h2M6.3 6.3l1.4 1.4M16.3 16.3l1.4 1.4M6.3 17.7l1.4-1.4M16.3 7.7l1.4-1.4"/><path d="M3 9a9.5 9.5 0 0 1 14-5.5M21 15a9.5 9.5 0 0 1-14 5.5"/></svg>
        <h3><span class="accent">Systems</span> Integration</h3>
        <p>Every nonprofit's IT applications are scattered and disconnected. Kestrel Point Technologies has decades of experience integrating these applications into a single cohesive system.</p>
      </div>
      <div class="tile tile-red">
        <svg viewBox="0 0 24 24" aria-hidden="true"><path d="M6 2h9l4 4v16H6z"/><path d="M15 2v4h4M9 11h7M9 14h7M9 17h7"/></svg>
        <h3>Business Intelligence &amp; Reporting</h3>
        <p>Kestrel Point Technologies can wrestle all of an organization's data into simple executive dashboards and reports.</p>
      </div>
      <div class="tile tile-light">
        <svg viewBox="0 0 24 24" aria-hidden="true"><path d="M7 17a4 4 0 0 1-.5-8 6 6 0 0 1 11.5 1.5 3.3 3.3 0 0 1-.5 6.5"/><path d="M12 11v10M9 18l3 3 3-3"/></svg>
        <h3><span class="accent">Cloud</span> Migration</h3>
        <p>Reduce IT costs by migrating to the latest cloud solutions</p>
      </div>
      <div class="tile tile-red">
        <svg viewBox="0 0 24 24" aria-hidden="true"><ellipse cx="12" cy="5" rx="7" ry="2.5"/><path d="M5 5v14c0 1.4 3.1 2.5 7 2.5s7-1.1 7-2.5V5M5 9.7c0 1.4 3.1 2.5 7 2.5s7-1.1 7-2.5M5 14.3c0 1.4 3.1 2.5 7 2.5s7-1.1 7-2.5"/></svg>
        <h3>Member Donor Database</h3>
        <p>Kestrel Point Technologies' GiveLedger Member / Donor CRM system is fully customized for each client meeting the unique needs of your organization.</p>
      </div>
    </section>
  </article>
</div>
</body>
</html>
```